skyPARLOR Helicopter Tour WordPress Website Design

SkyPARLOR (skyparlor-example.com) is a premium helicopter tour company offering scenic flights in two Florida cities: Tampa and Sarasota. We are seeking a full Wordpress website redesign that is modern, upbeat, inviting, and highly conversion‑focused. The new site should feel energetic and trustworthy, reflect the excitement of helicopter sightseeing, and maintain our recognizable SkyPARLOR color palette—while updating the overall look to feel fresh, clean, and current.
The website must be SEO‑friendly, mobile‑optimized, and easy to navigate. It should highlight our 5‑star customer reviews, showcase our tours clearly, and integrate seamlessly with TrailDock for instant online booking. The design should support a premium aviation experience while remaining friendly and accessible to tourists, families, couples, and adventure seekers.

These elements are essential and must be included in the design:

Brand & UX:
- Modern, upbeat, inviting design
- SEO‑friendly structure and layout
- Easy navigation and clear user flow
- Light grey “SP” background logo watermark (as used on current site)
- Clean, aviation‑inspired typography and layout

Conversion Features:
- Instant booking above the fold (TrailDock integration)
- Live Orbin Ratings carousel
- Tour comparison table (duration, route, price, etc.)
- FAQ expandable section
- Gift Cards page (highlighted as a major offering)
- What to Expect timeline (Arrive → Check‑In → Safety Briefing → Flight → Photos)
- Weather transparency widget (clear messaging about weather‑dependent flights

Content Structure:
- Separate pages for Tampa, Sarasota, and Gender Reveal Flights
- Pilot/Team profiles with short bios
- Highlighted features:
- Doors‑Off option
- Sunset flights
- Romantic packages
- Champagne add‑ons

Colors:
Use the existing SkyPARLOR palette as the foundation, but modernize it.
- Background: Clean with the light grey “SP” watermark integrated tastefully.
The overall color direction should feel bright, premium, energetic, and trustworthy

Target Market(s)

Tourists visiting Tampa or Sarasota, Families looking for memorable activities, Couples seeking romantic experiences (sunset flights, proposals, anniversaries), Adventure seekers and content creators, Locals celebrating birthdays, holidays, or special occasions, Gender reveal clients looking for a unique aerial reveal experience

Industry/Entity Type

Travel & Tourism / Aviation / Helicopter Tours / Experience‑based Activities

Requirements
Must have
• These elements are essential and must be included in the design: Brand & UX - Modern, upbeat, inviting design / SEO‑friendly structure and layout / Easy navigation and clear user flow / Light grey “SP” background logo watermark (as used on current site) / Clean, aviation‑inspired typography and layout
Nice to have
• Interactive route map showing flight paths / Subtle motion or parallax effects in hero sections / Animated icons or micro‑interactions / Social media integration (Instagram grid, TikTok clips) / Sticky mobile booking bar / Video header or short aerial footage loop / Subtle aviation‑themed graphic elements (rotor blur, sky gradients, etc.
Should not have
• No dark, heavy, or overly moody themes / No outdated fonts or overly playful typography / No cluttered layouts or excessive text blocks / No stocky, generic tourism imagery / No slow‑loading animations or heavy effects that hurt SEO

```html
<!DOCTYPE html>
<html lang="en">
<head>
<meta charset="utf-8">
<title>SkyPARLOR – Helicopter Tours in Tampa &amp; Sarasota</title>
<link href="https://fonts.googleapis.com/css2?family=Poppins:wght@300;400;500;600;700&display=swap" rel="stylesheet">
<style>
:root{
  --blue:#1d5fa9;
  --blue-dark:#174f8f;
  --navy:#1b3f73;
  --sky:#eef4fb;
  --ink:#1f2228;
  --muted:#5d6470;
  --line:#d9e2ee;
  --red:#e3262b;
  --footer:#1e2023;
  --white:#ffffff;
  --star:#f5a623;
}
*{box-sizing:border-box;margin:0;padding:0}
html,body{width:1200px;height:5199px;overflow:hidden}
body{font-family:"Poppins",sans-serif;color:var(--ink);background:var(--white);position:relative}
section,header,footer{position:relative;width:1200px;overflow:hidden}
.abs{position:absolute}
.ph{position:absolute}
.btn{position:absolute;display:flex;align-items:center;justify-content:center;border-radius:30px;background:var(--blue);color:#fff;font-weight:500;font-size:15px}
.section-title{position:absolute;left:0;width:1200px;text-align:center;font-size:40px;font-weight:400;color:var(--ink);display:flex;justify-content:center;align-items:center;gap:14px}
.section-title b{font-weight:700}
.mark{font-weight:700;font-size:40px;color:#c9ced6;letter-spacing:-1px}
.arrow{position:absolute;width:34px;height:34px;border-radius:50%;border:2px solid var(--blue);display:flex;align-items:center;justify-content:center}

/* header */
.site-header{height:128px;box-shadow:0 2px 8px rgba(0,0,0,.08);z-index:2}
.topbar{position:absolute;left:420px;top:0;width:545px;height:56px;background:var(--blue-dark);clip-path:polygon(20px 0,100% 0,100% 100%,0 100%);display:flex;align-items:center;gap:20px;padding-left:50px;color:#fff;font-size:15px;font-weight:500}
.topbar .dot{width:14px;height:14px;border-radius:50%;background:#fff;display:inline-block}
.weather{position:absolute;left:965px;top:0;width:235px;height:56px;background:#7aa3d4;color:#fff;font-size:15px;font-weight:500;display:flex;align-items:center;gap:10px;padding-left:58px}
.logo{position:absolute;left:105px;top:50px;font-size:30px;font-weight:600;color:var(--blue);display:flex;align-items:center;gap:8px}
.logo i{width:14px;height:14px;border-radius:50%;background:var(--blue);display:block}
.nav{position:absolute;left:370px;top:80px;display:flex;gap:38px;font-size:15px;color:#333}
.nav .active{color:var(--blue);font-weight:600}
.contact-btn{left:970px;top:74px;width:120px;height:40px;font-size:15px}

/* hero */
.hero{height:662px;background:linear-gradient(110deg,#2f64a8 0%,#4f7db6 40%,#7e93a9 70%,#a9876a 100%)}
.hero h1{position:absolute;left:110px;top:295px;color:#fff;font-size:50px;font-weight:600;line-height:62px}
.hero-photo{inset:0}
.hero p{position:absolute;left:110px;top:432px;color:#fff;font-size:21px}
.hero .book{left:110px;top:488px;width:236px;height:52px;background:rgba(29,95,169,.9);border:2px solid #fff;font-size:15px;font-weight:600}
.play{position:absolute;left:402px;top:475px;width:72px;height:72px;border-radius:50%;background:var(--red);box-shadow:0 0 0 8px rgba(227,38,43,.35);display:flex;align-items:center;justify-content:center}
.hero-curve{position:absolute;left:0;bottom:0}

/* expect */
.expect{height:478px}
.expect .sub{position:absolute;top:130px;width:1200px;text-align:center;font-size:17px;color:#333}
.step{position:absolute;top:208px;width:201px;height:178px;background:var(--blue);border-radius:10px;color:#fff;text-align:center;padding:68px 14px 0}
.step h3{font-size:20px;font-weight:600;margin-bottom:8px}
.step p{font-size:12px;line-height:20px}
.step .ico{position:absolute;left:64px;top:-30px;width:74px;height:74px;border-radius:50%;background:var(--blue);border:4px solid #fff;display:flex;align-items:center;justify-content:center}

/* features */
.features{height:568px;background:var(--sky)}
.feature{position:absolute;top:170px;width:216px;height:322px;background:#fff;border-radius:10px;box-shadow:0 4px 10px rgba(0,0,0,.15);overflow:hidden}
.feature .photo{height:262px}
.feature span{display:block;text-align:center;font-size:17px;font-weight:500;margin-top:20px}

/* comparison */
.compare{height:694px}
.tours{position:absolute;left:111px;top:167px;width:979px;border-collapse:collapse;border-radius:10px;overflow:hidden;font-size:16px}
.tours th{background:#2f62a8;color:#fff;font-weight:500;height:70px;font-size:18px;border-right:1px solid #6f93c4}
.tours td{height:83px;text-align:center;font-weight:500;border-right:1px solid var(--blue)}
.tours td:first-child{text-align:left;padding-left:30px}
.tours tr:nth-child(odd) td{background:#eef1f6}
.tours tr:nth-child(even) td{background:#fafbfd}
.tours th:last-child,.tours td:last-child{border-right:none}
.compare .book-flight{left:503px;top:545px;width:195px;height:50px;background:#3f6ca9}

/* reviews */
.reviews{height:436px;background:var(--blue)}
.reviews .section-title{color:#fff}
.reviews .mark{color:rgba(255,255,255,.55)}
.review{position:absolute;top:151px;width:302px;height:198px;background:#fff;border-radius:8px;padding:22px 16px;font-size:13px;line-height:25px;color:#444}
.review .who{position:absolute;left:16px;top:138px;font-weight:600;color:#222;font-size:14px}
.review .who em{font-style:normal;color:var(--star);margin-left:4px}
.review .when{position:absolute;left:16px;top:164px;color:#888;font-size:13px}
.review .badge{position:absolute;right:20px;top:144px;width:20px;height:20px;border-radius:50%;background:#5b8bd2}
.reviews .arrow{border-color:#fff}

/* city */
.city{height:559px;background:#f3f7fb}
.city .title{position:absolute;left:108px;top:85px;display:flex;gap:14px;align-items:center;font-size:44px;font-weight:600}
.city .body{position:absolute;left:111px;top:170px;width:486px;font-size:15px;line-height:27px;color:#333;text-align:justify}
.city .body p{margin-bottom:27px}
.city .more{left:111px;top:427px;width:142px;height:50px}
.city-photo{left:672px;top:0;width:528px;height:559px}

/* faq */
.faq{height:746px}
.faq-item{position:absolute;left:110px;width:978px;height:54px;background:#fff;border-radius:4px;box-shadow:0 2px 8px rgba(0,0,0,.14);display:flex;align-items:center;justify-content:space-between;padding:0 20px;font-size:16px}
.plus{width:22px;height:22px;border-radius:50%;background:#6d6f73;color:#fff;font-size:18px;line-height:22px;text-align:center}
.faq .view{left:528px;top:606px;width:145px;height:52px}

/* portfolio */
.portfolio{height:519px;background:#f4f8fc}
.shot{position:absolute;top:152px;height:275px;border-radius:10px}
.social-dot{position:absolute;left:240px;top:125px;width:50px;height:50px;border-radius:50%;background:#d9458b;border:4px solid #fff}

/* footer */
.site-footer{height:412px;background:var(--footer);color:#fff}
.site-footer .flogo{position:absolute;left:105px;top:152px;font-size:34px;font-weight:600;color:#5f9be0;display:flex;align-items:center;gap:10px}
.site-footer .flogo i{width:16px;height:16px;border-radius:50%;background:#5f9be0;display:block}
.copy{position:absolute;left:111px;top:253px;font-size:15px}
.socials{position:absolute;left:111px;top:304px;display:flex;gap:12px}
.socials i{width:14px;height:14px;border-radius:50%;background:#fff;display:block}
.links{position:absolute;left:397px;top:96px}
.links h4{font-size:21px;font-weight:600;margin-bottom:6px}
.links li{list-style:none;font-size:15px;line-height:32px}
.map{position:absolute;left:655px;top:103px;width:433px;height:224px;border:5px solid #fff;background:linear-gradient(90deg,#3f6faf 0 28%,#dfe6ee 28% 100%)}
</style>
</head>
<body>

<header class="site-header">
  <div class="topbar">
    <span><span class="dot"></span>&nbsp; (555) 014-2290</span>
    <span><span class="dot"></span>&nbsp; info@skyparlor-example.com</span>
  </div>
  <div class="weather">
    <svg width="26" height="22" viewBox="0 0 26 22"><circle cx="9" cy="8" r="5" fill="#fff"/><path d="M8 20h13a4 4 0 0 0 0-8 6 6 0 0 0-11 1 3.5 3.5 0 0 0-2 7z" fill="#fff"/></svg>
    Weather Policy
  </div>
  <div class="logo"><i></i>SkyPARLOR</div>
  <nav class="nav">
    <span class="active">Home</span><span>Sarasota</span><span>Tampa</span><span>Gender Reveal Flights</span><span>Gift Cards</span>
  </nav>
  <div class="btn contact-btn">Contact Us</div>
</header>

<section class="hero">
  <div class="ph hero-photo" role="img" aria-label="Smiling couple wearing aviation headsets inside a helicopter cockpit" style="background:linear-gradient(110deg,#2f64a8 0%,#4b7ab4 38%,#8494a8 65%,#b38b6c 85%,#6f5a4b 100%)"></div>
  <h1>The Ultimate<br>Helicopter Experience</h1>
  <p>Say <b>Yes</b> to new Adventures.</p>
  <div class="btn book">Book Your Sky Parlor &nbsp;›</div>
  <div class="play"><svg width="26" height="28" viewBox="0 0 26 28"><path d="M3 2l21 12L3 26z" fill="#fff"/></svg></div>
  <svg class="hero-curve" width="1200" height="130" viewBox="0 0 1200 130">
    <path d="M0 130 L0 122 C120 80 220 30 330 20 L1200 106 L1200 130 Z" fill="#fff"/>
    <path d="M330 12 L1200 96 L1200 104 L330 20 C250 26 150 70 60 110 C150 60 240 18 330 12Z" fill="#1d5fa9"/>
  </svg>
</section>

<section class="expect">
  <h2 class="section-title" style="top:40px"><span class="mark">SP</span><span>What to <b>Expect</b></span></h2>
  <p class="sub">From arrival to touchdown, here’s how your Sky Parlor experience unfolds.</p>
  <div class="step" style="left:47px"><div class="ico"><svg width="26" height="30" viewBox="0 0 26 30"><path d="M13 2a10 10 0 0 1 10 10c0 8-10 16-10 16S3 20 3 12A10 10 0 0 1 13 2z" fill="none" stroke="#fff" stroke-width="2.5"/><circle cx="13" cy="12" r="3.5" fill="#fff"/></svg></div><h3>Arrive</h3><p>Arrive a few minutes early and check in with our friendly ground team.</p></div>
  <div class="step" style="left:273px"><div class="ico"><svg width="28" height="28" viewBox="0 0 28 28"><rect x="3" y="3" width="22" height="22" rx="3" fill="none" stroke="#fff" stroke-width="2.5"/><circle cx="18" cy="12" r="3" fill="#fff"/><path d="M12 20a6 6 0 0 1 12 0z" fill="#fff"/><path d="M5 14h6m-3-3l3 3-3 3" stroke="#fff" stroke-width="2" fill="none"/></svg></div><h3>Check-In</h3><p>Confirm your booking, store personal items, and get ready to fly.</p></div>
  <div class="step" style="left:499px"><div class="ico"><svg width="28" height="28" viewBox="0 0 28 28"><circle cx="12" cy="13" r="9" fill="none" stroke="#fff" stroke-width="2.5"/><path d="M18 14l4-2 4 2v4c0 3-4 5-4 5s-4-2-4-5z" fill="#fff"/></svg></div><h3>Safety Briefing</h3><p>Meet your pilot and receive a clear, professional safety overview.</p></div>
  <div class="step" style="left:725px"><div class="ico"><svg width="28" height="28" viewBox="0 0 24 24"><path d="M21 16v-2l-8-5V3.5a1.5 1.5 0 0 0-3 0V9l-8 5v2l8-2.5V19l-2 1.5V22l3.5-1 3.5 1v-1.5L13 19v-5.5z" fill="#fff"/></svg></div><h3>Flight</h3><p>Enjoy a smooth, unforgettable helicopter tour with stunning aerial</p></div>
  <div class="step" style="left:951px"><div class="ico"><svg width="28" height="26" viewBox="0 0 28 26"><rect x="2" y="3" width="24" height="20" rx="3" fill="none" stroke="#fff" stroke-width="2.5"/><path d="M5 20l7-8 5 5 3-3 4 6z" fill="#fff"/><circle cx="20" cy="9" r="2.5" fill="#fff"/></svg></div><h3>Photos</h3><p>Capture photos and videos before and after your flight to remember the experience.</p></div>
</section>

<section class="features">
  <h2 class="section-title" style="top:70px"><span class="mark">SP</span><span>Our <b>Features</b></span></h2>
  <div class="feature" style="left:111px"><div class="photo" role="img" aria-label="Passengers in a doors-off helicopter" style="background:linear-gradient(160deg,#9aa4ad,#4a4f55)"></div><span>Doors-Off</span></div>
  <div class="feature" style="left:365px"><div class="photo" role="img" aria-label="Helicopter silhouetted against a golden sunset" style="background:linear-gradient(180deg,#e0a642,#b06a1c 60%,#6a3e12)"></div><span>Sunset flights</span></div>
  <div class="feature" style="left:619px"><div class="photo" role="img" aria-label="Couple sharing a romantic moment outdoors" style="background:linear-gradient(160deg,#d9d2c6,#8a7a6a)"></div><span>Romantic packages</span></div>
  <div class="feature" style="left:873px"><div class="photo" role="img" aria-label="Pilot flying over a city skyline" style="background:linear-gradient(180deg,#9ab7d3,#5b6f83 60%,#2f3a45)"></div><span>Champagne add-ons</span></div>
</section>

<section class="compare">
  <h2 class="section-title" style="top:100px"><span class="mark">SP</span><span>Tour <b>Comparison</b></span></h2>
  <table class="tours">
    <thead><tr><th>TOUR</th><th>LOCATION</th><th>DURATION</th><th>HIGHLIGHT</th><th>PRICE</th></tr></thead>
    <tbody>
      <tr><td>Tampa Skyline</td><td>Tampa</td><td>20 min</td><td>Downtown views</td><td>From $567.89</td></tr>
      <tr><td>Gulf Coast</td><td>Sarasota</td><td>30 min</td><td>Beaches &amp; sunset</td><td>From $567.89</td></tr>
      <tr><td>Gender Reveal</td><td>Custom</td><td>Custom</td><td>Smoke reveal</td><td>From $567.89</td></tr>
    </tbody>
  </table>
  <div class="btn book-flight">Book The Flight</div>
</section>

<section class="reviews">
  <h2 class="section-title" style="top:60px"><span class="mark">SP</span><span>What Our <b>Customer Says</b></span></h2>
  <div class="arrow" style="left:33px;top:233px"><svg width="14" height="14" viewBox="0 0 14 14"><path d="M13 7H2m5-5L2 7l5 5" stroke="#fff" stroke-width="2" fill="none"/></svg></div>
  <div class="arrow" style="left:1133px;top:233px"><svg width="14" height="14" viewBox="0 0 14 14"><path d="M1 7h11M7 2l5 5-5 5" stroke="#fff" stroke-width="2" fill="none"/></svg></div>
  <div class="review" style="left:110px">This was an Early Christmas gift for my 9yr old special needs son. Everything exceeded my expectations and Marco our pilot did an amazing.<div class="who">Dana Price<em>★★★★★</em></div><div class="when">2 weeks ago</div><div class="badge"></div></div>
  <div class="review" style="left:448px">Such a great experience! My husband booked us the romantic flight as a suprise &amp; it was absolutely adorable. Definitely need to have a good tour<div class="who">Lena Moreno<em>★★★★★</em></div><div class="when">2 weeks ago</div><div class="badge"></div></div>
  <div class="review" style="left:786px">Amazing experience. Marco was our pilot and he was awesome. Just great vibes.<div class="who">TJ Walters<em>★★★★★</em></div><div class="when">2 weeks ago</div><div class="badge"></div></div>
</section>

<section class="city">
  <div class="title"><span class="mark">SP</span>Sarasota</div>
  <div class="body">
    <p>Sky Parlor offers unforgettable Sarasota helicopter tours that showcase the best of Florida’s Gulf Coast from the sky. From Siesta Key and Lido Key to Downtown Sarasota, you can design your own custom aerial adventure or choose from our most popular sightseeing flights.</p>
    <p>Whether you prefer a smooth, air-conditioned ride or the thrill of a doors-off helicopter tour, every flight delivers stunning views and unforgettable moments from takeoff to landing.</p>
  </div>
  <div class="btn more">Read More</div>
  <div class="ph city-photo" role="img" aria-label="Aerial view of downtown Sarasota marina at dusk" style="background:linear-gradient(180deg,#c9c3bb 0%,#7d8a9a 25%,#3d4f66 60%,#22303f 100%)"></div>
  <div class="arrow" style="left:33px;top:270px"><svg width="14" height="14" viewBox="0 0 14 14"><path d="M13 7H2m5-5L2 7l5 5" stroke="#1d5fa9" stroke-width="2" fill="none"/></svg></div>
  <div class="arrow" style="left:1131px;top:270px;border-color:#fff"><svg width="14" height="14" viewBox="0 0 14 14"><path d="M1 7h11M7 2l5 5-5 5" stroke="#fff" stroke-width="2" fill="none"/></svg></div>
</section>

<section class="faq">
  <h2 class="section-title" style="top:80px"><span class="mark">SP</span><span>Frequently <b>Asked Questions</b></span></h2>
  <div class="faq-item" style="top:178px">1) Excepteur sint occaecat cupidatat non proident, sunt in culpa qui officia?<span class="plus">+</span></div>
  <div class="faq-item" style="top:245px">2) Duis aute irure dolor in reprehenderit in voluptate velit?<span class="plus">+</span></div>
  <div class="faq-item" style="top:311px">3) Excepteur sint occaecat cupidatat non proident, sunt in culpa qui officia?<span class="plus">+</span></div>
  <div class="faq-item" style="top:378px">4) Duis aute irure dolor in reprehenderit in voluptate velit?<span class="plus">+</span></div>
  <div class="faq-item" style="top:445px">5) Excepteur sint occaecat cupidatat non proident, sunt in culpa qui officia?<span class="plus">+</span></div>
  <div class="faq-item" style="top:511px">6) Duis aute irure dolor in reprehenderit in voluptate velit?<span class="plus">+</span></div>
  <div class="btn view">View More</div>
</section>

<section class="portfolio">
  <h2 class="section-title" style="top:60px"><span class="mark">SP</span><span>Our <b>Portfolios</b></span></h2>
  <div class="arrow" style="left:33px;top:272px"><svg width="14" height="14" viewBox="0 0 14 14"><path d="M13 7H2m5-5L2 7l5 5" stroke="#1d5fa9" stroke-width="2" fill="none"/></svg></div>
  <div class="arrow" style="left:1133px;top:272px"><svg width="14" height="14" viewBox="0 0 14 14"><path d="M1 7h11M7 2l5 5-5 5" stroke="#1d5fa9" stroke-width="2" fill="none"/></svg></div>
  <div class="shot" style="left:111px;width:309px;background:linear-gradient(150deg,#c9b9a6,#8a6e58 60%,#5a463a)" role="img" aria-label="Couple looking out a helicopter window"></div>
  <div class="shot" style="left:432px;width:401px;background:linear-gradient(160deg,#9fc2dc,#6b7f8c 50%,#2e3a44)" role="img" aria-label="Passengers with headsets in a helicopter cockpit"></div>
  <div class="shot" style="left:843px;width:244px;background:linear-gradient(160deg,#4a4c50,#1f2124)" role="img" aria-label="Helicopter parked on a dark helipad, viewed from above"></div>
  <div class="social-dot"></div>
  <div class="play" style="left:235px;top:262px;width:52px;height:52px;box-shadow:none"><svg width="18" height="20" viewBox="0 0 26 28"><path d="M3 2l21 12L3 26z" fill="#fff"/></svg></div>
</section>

<footer class="site-footer">
  <div class="flogo"><i></i>SkyPARLOR</div>
  <div class="copy">©2026.SkyParlor-example.com</div>
  <div class="socials"><i></i><i></i><i></i></div>
  <div class="links">
    <h4>Quick Links</h4>
    <ul><li>» Home</li><li>» Sarasota</li><li>» Tampa</li><li>» Gender Reveal Flights</li><li>» Gift Cards</li><li>» Contact Us</li></ul>
  </div>
  <div class="map" role="img" aria-label="Map of Tampa and Sarasota tour locations"></div>
</footer>

</body>
</html>
```